Wordpress Web Design & Coding for velcorahealth.ca

We need a website for a new investment company that is visually grabbing and vibrant. We would like to see a web page that displays trust, growth and confidence. Needs to be responsive and mobile friendly for all browsers and coded for both Android & IOS.

Open to the number of pages and menu items. I selected 4 but if you feel the layout would work better with less I am open to this. Need to sell the people (management team/related businesses) and then show where the invested money will be going (upcoming projects).

Company Info:

Vel Cora is an investment company put together by a group of seasoned business professionals who have come together to combine decades of success in the real estate development, management, financing and medical services. The company will be a full service company offering turn key solutions for medical professionals.

Vel-Cora will focus on providing a full range of services via a group of distinct companies to deliver newly emerging needs of the medical community. The end goal will be to create complete solutions for individuals in the medical community. Our group has experience and success with the conceptualization, construction and financing of medical and dental clinic spaces. Vel-Cora Solutions will be established to accommodate all areas of the development and creation of clinics for medical professionals from building construction to equipment financing and administrations.

You can mention these companies and take photos from their websites. You can also use stock photos.

Our construction partner:
https://318bld.com/projects/

Our equipment leasing partner:
https://www.norvixa.com/

Our Management Team and medical partners

Gil Parish
https://www.ourfirmstance.ca/

Dietmar Vellasquin
https://www.gshdentalservices.com/about-us

PROPOSED PROJECTS (see attachment for details)
Pinegrove Business Park
Holtmere Business Park
Mt. Corwin Ridge Professional

Target Market(s)

Investors

Industry/Entity Type

Investment

Coding

Coded - Design and coding required

Number of Pages Required

4 page

Font styles to use
Sans Serif

Requirements
Must have
• Wordpress – must be both desktop and mobile friendly with fast page load speed
Ability to edit after ourselves in Wordpress
Attractive home page with logo etc.
Logo colours are: for the blue the pantone color is #0355a3
and for the green is #8cc63f

Sections, about us, what we do/services we provide, contact us

```html
<!DOCTYPE html>
<html lang="en">
<head>
<meta charset="utf-8">
<title>Vel-Cora Solutions</title>
<link rel="stylesheet" href="https://fonts.googleapis.com/css2?family=Montserrat:wght@400;500;600;700&display=swap">
<style>
:root{
  --blue:#0355a3;
  --blue-light:#5aa9e6;
  --green:#8cc63f;
  --ink:#1e1e1e;
  --text:#3a3a3a;
  --muted:#6b6b6b;
  --soft:#f3f3f3;
  --line:#d9d9d9;
  --white:#ffffff;
}
*{margin:0;padding:0;box-sizing:border-box}
html,body{width:1200px;height:3468px;overflow:hidden;background:var(--white)}
body{font-family:"Montserrat",Arial,sans-serif;color:var(--text);position:relative}
.abs{position:absolute}
.section-title{position:absolute;left:0;width:1200px;text-align:center;font-size:28px;font-weight:500;letter-spacing:1px;color:var(--blue);z-index:1}
.section-title b{color:var(--green);font-weight:600}
.section-title::after{content:"";display:block;width:36px;height:3px;background:var(--green);margin:12px auto 0}
.btn{position:absolute;background:var(--blue);color:var(--white);font-size:14px;font-weight:600;display:flex;align-items:center;justify-content:center;border-radius:2px}
.link{color:var(--blue);font-size:11px;font-weight:600;text-decoration:underline}

/* header */
.site-header{position:absolute;top:0;left:0;width:1200px;height:77px;border-top:3px solid var(--blue);background:var(--white);box-shadow:0 2px 6px rgba(0,0,0,.06);z-index:2}
.brand{position:absolute;left:141px;top:22px;display:flex;align-items:center;gap:8px;font-size:22px;font-weight:700;color:var(--blue)}
.brand i{width:14px;height:14px;background:var(--green);display:block}
.nav{position:absolute;top:30px;font-size:12px;font-weight:500;color:var(--ink)}
.nav.active{color:var(--blue);font-weight:600}
.nav-sep{position:absolute;top:29px;width:1px;height:17px;background:var(--line)}

/* hero */
.hero{position:absolute;top:77px;left:0;width:1200px;height:494px;background:#efefef}
.hero-photo{position:absolute;left:593px;top:0;width:607px;height:494px;background:linear-gradient(100deg,#efefef 0%,#dfe6ee 30%,#cfdbe8 60%,#b9cde2 100%)}
.hero-eyebrow{position:absolute;left:141px;top:226px;font-size:20px;font-weight:500;color:var(--ink);letter-spacing:.5px}
.hero-title{position:absolute;left:141px;top:261px;font-size:35px;font-weight:600;color:var(--blue);letter-spacing:1px}
.hero-title b{color:var(--green);font-weight:700}
.hero-text{position:absolute;left:141px;top:308px;font-size:17px;line-height:25px;color:var(--ink);width:440px}

/* about */
.about-photo{position:absolute;left:141px;top:641px;width:433px;height:339px;border:3px solid var(--blue);border-radius:14px;background:linear-gradient(135deg,#e9eef3,#c9d6e3 55%,#7fa3c8)}
.about-title{position:absolute;left:614px;top:634px;font-size:28px;font-weight:500;color:var(--blue);letter-spacing:1px}
.about-title b{color:var(--green);font-weight:600}
.about-title::after{content:"";display:block;width:36px;height:3px;background:var(--green);margin-top:10px}
.about-lead{position:absolute;left:614px;top:690px;width:444px;font-size:13.2px;line-height:23px;text-align:justify;color:var(--ink)}
.about-body{position:absolute;left:614px;top:811px;width:444px;font-size:10.6px;line-height:20.4px;text-align:justify;color:var(--muted)}

/* services */
.services{position:absolute;top:1050px;left:0;width:1200px;height:434px;background:var(--soft)}
.service{position:absolute;top:140px;width:220px;text-align:center}
.service .ring{width:124px;height:124px;margin:0 auto;border:4px solid var(--green);border-radius:50%;background:var(--white);display:flex;align-items:center;justify-content:center}
.service h3{margin-top:20px;font-size:15px;font-weight:600;color:var(--ink)}
.service p{margin-top:6px;font-size:11.5px;line-height:15px;color:var(--text)}
.service .link{display:block;margin-top:7px}

/* projects */
.project{position:absolute;top:1616px;width:282px;height:259px;background:var(--white);box-shadow:0 3px 12px rgba(0,0,0,.12);text-align:center}
.project .pic{height:189px;background:linear-gradient(180deg,#b9cde3 0%,#e9ecef 45%,#9aa1a6 100%)}
.project h3{margin-top:15px;font-size:15px;font-weight:600;color:var(--ink)}
.project .link{display:block;margin-top:6px}

/* team */
.team{position:absolute;top:1947px;left:0;width:1200px;height:581px;background:#f5f5f5}
.team-photo{position:absolute;left:727px;top:2068px;width:243px;height:370px;background:linear-gradient(180deg,#e9ecef,#8a9099 45%,#4a5058)}
.member-name{position:absolute;left:214px;top:2155px;font-size:19px;font-weight:600;color:var(--ink)}
.member-bio{position:absolute;left:214px;top:2196px;width:475px;font-size:14.2px;line-height:24px;color:var(--ink)}
.social{position:absolute;top:2347px;width:28px;height:28px;border-radius:50%;background:var(--blue)}
.arrow{position:absolute;top:2238px;width:32px;height:32px;border-radius:50%;display:flex;align-items:center;justify-content:center}

/* partners + contact */
.lower{position:absolute;top:2528px;left:0;width:1200px;height:900px;background:linear-gradient(180deg,#ffffff 0%,#f4f6f9 35%,#c9d9ec 62%,#3f7fc2 85%,#0b4f9e 100%)}
.partner{position:absolute;top:2663px;width:171px;height:80px;background:var(--white);box-shadow:0 2px 8px rgba(0,0,0,.08);display:flex;flex-direction:column;align-items:center;justify-content:center;color:var(--ink)}
.partner strong{font-size:17px;font-weight:600}
.partner span{font-size:7px;letter-spacing:.5px;margin-top:3px;color:var(--muted)}
.contact-card{position:absolute;left:249px;top:2828px;width:706px;height:404px;background:#f2f2f2;border:5px solid var(--white);border-radius:10px;box-shadow:0 18px 26px rgba(3,85,163,.35)}
.field{position:absolute;height:37px;background:var(--white);border:1px solid var(--line);font-size:11px;color:var(--text);padding:12px 14px}
.contact-info{position:absolute;top:3317px;display:flex;gap:14px;align-items:flex-start;color:var(--white);font-size:14px;line-height:20px}
.contact-info b{font-weight:600}
.info-icon{width:33px;height:33px;border:2px solid var(--white);border-radius:50%;display:flex;align-items:center;justify-content:center;flex:none}
.info-sep{position:absolute;top:3313px;width:1px;height:50px;background:rgba(255,255,255,.3)}
.bottom-bar{position:absolute;top:3428px;left:0;width:1200px;height:40px;background:var(--green);color:var(--white);font-size:12.5px}
.bottom-bar .copy{position:absolute;left:141px;top:13px}
.bottom-bar .dot{position:absolute;top:16px;width:8px;height:8px;background:var(--white);border-radius:50%}
</style>
</head>
<body>

<header class="site-header">
  <div class="brand"><i></i>Vel-Cora</div>
  <span class="nav active" style="left:507px">HOME</span>
  <span class="nav-sep" style="left:591px"></span>
  <span class="nav" style="left:638px">ABOUT US</span>
  <span class="nav-sep" style="left:750px"></span>
  <span class="nav" style="left:795px">OUR SERVICES</span>
  <span class="nav-sep" style="left:930px"></span>
  <span class="nav" style="left:979px">CONTACT US</span>
</header>

<section class="hero">
  <div class="hero-photo" role="img" aria-label="Doctor touching a grid of blue hexagonal medical icons"></div>
</section>
<div class="hero-eyebrow">WELCOME TO</div>
<div class="hero-title">VEL-CORA <b>SOLUTIONS</b></div>
<p class="hero-text">Vel Cora is an investment company put together by a group of seasoned business professionals</p>
<div class="btn" style="left:141px;top:378px;width:116px;height:34px">Read More</div>

<div class="about-photo" role="img" aria-label="Businessman and nurse reviewing a clipboard in a clinic"></div>
<h2 class="about-title">ABOUT <b>US</b></h2>
<p class="about-lead">We are a group of seasoned business professionals who have come together to combine decades of success in the real estate development, management, financing and medical services. The company will be a full service company offering turnkey solutions for medical professionals.</p>
<p class="about-body">Vel-Cora will focus on providing a full range of services via a group of distinct companies to deliver newly emerging needs of the medical community. The end goal will be to create complete solutions for individuals in the medical community. Our group has experience and success with the conceptualization, construction and financing of medical and dental clinic spaces. Vel-Cora Solutions will be established to accommodate all areas of the development...</p>
<div class="btn" style="left:614px;top:945px;width:117px;height:35px">Read More</div>

<section class="services">
  <h2 class="section-title" style="top:64px">OUR <b>SERVICES</b></h2>
  <div class="service" style="left:132px">
    <div class="ring"><svg width="58" height="58" viewBox="0 0 58 58" fill="none" stroke="#0355a3" stroke-width="2.5"><path d="M8 10v10h42V10M16 20l-4 8M42 20l4 8M22 24h14M12 34h34v6H12zM16 40v12M42 40v12M29 20v4"/><circle cx="12" cy="30" r="3"/><circle cx="46" cy="30" r="3"/></svg></div>
    <h3>Operating Hospitals</h3>
    <p>Lorem ipsum dolor sit amet, conse ctetuer adipiscing elit.</p>
    <span class="link">READ MORE</span>
  </div>
  <div class="service" style="left:371px">
    <div class="ring"><svg width="58" height="58" viewBox="0 0 58 58" fill="none" stroke="#0355a3" stroke-width="2.5"><path d="M8 52h42M14 52V24h12V8h14v44M40 24h8v28M18 30h4M18 38h4M18 46h4M30 26h6M30 34h6M30 42h6M33 12v8M29 16h8"/></svg></div>
    <h3>Medical Centers</h3>
    <p>Lorem ipsum dolor sit amet, conse ctetuer adipiscing elit.</p>
    <span class="link">READ MORE</span>
  </div>
  <div class="service" style="left:609px">
    <div class="ring"><svg width="58" height="58" viewBox="0 0 58 58" fill="none" stroke="#0355a3" stroke-width="2.5"><path d="M19 14q10-8 20 0v6H19zM29 14v4M27 16h4M20 22q0 12 9 12t9-12M12 54q0-16 17-18 17 2 17 18zM22 40v8M36 40q4 4 0 10"/><circle cx="22" cy="50" r="2"/></svg></div>
    <h3>Operating Nursing Homes</h3>
    <p>Lorem ipsum dolor sit amet, conse ctetuer adipiscing elit.</p>
    <span class="link">READ MORE</span>
  </div>
  <div class="service" style="left:849px">
    <div class="ring"><svg width="58" height="58" viewBox="0 0 58 58" fill="none" stroke="#0355a3" stroke-width="2.5"><path d="M6 50h46M10 50V26h38v24M20 26V10h18v16M29 13v10M24 18h10M15 32h4M23 32h4M31 32h4M39 32h4M15 40h4M23 40h4M31 40h4M39 40h4"/></svg></div>
    <h3>Hospice Care</h3>
    <p>Lorem ipsum dolor sit amet, conse ctetuer adipiscing elit.</p>
    <span class="link">READ MORE</span>
  </div>
</section>

<h2 class="section-title" style="top:1545px">UPCOMING <b>PROJECTS</b></h2>
<div class="project" style="left:141px"><div class="pic" role="img" aria-label="Two-storey business park building with trees"></div><h3>Pinegrove Business Park</h3><span class="link">READ MORE</span></div>
<div class="project" style="left:459px"><div class="pic" role="img" aria-label="Business park building with parking lot"></div><h3>Holtmere Business Park</h3><span class="link">READ MORE</span></div>
<div class="project" style="left:777px"><div class="pic" role="img" aria-label="White commercial building with storefront signs"></div><h3>Ashford Close</h3><span class="link">READ MORE</span></div>

<section class="team"></section>
<h2 class="section-title" style="top:2005px">MANAGEMENT <b>TEAM</b></h2>
<svg class="abs" style="left:0;top:2080px" width="1200" height="362" viewBox="0 0 1200 362" fill="none" stroke="#9a9a9a" stroke-width="1.3">
  <path d="M140 36V357H1058V5H939"/>
</svg>
<div class="team-photo" role="img" aria-label="Portrait of a doctor in a grey suit with arms crossed"></div>
<h3 class="member-name">Dr. Gil Parish</h3>
<p class="member-bio">Dr. Parish graduated with a degree in Family Medicine in 1983. He practiced medicine as a solo rural general practitioner for 6 years. He then completed a residency in obstetrics &amp; Gynecology at the university of Westbrook. Gil joined a group practice at the Harlow Crest Hospital, where he practiced for 24 years.</p>
<span class="social" style="left:215px"></span>
<span class="social" style="left:250px"></span>
<span class="social" style="left:285px"></span>
<div class="arrow" style="left:123px;background:#dcdcdc"><svg width="12" height="14" viewBox="0 0 12 14" fill="none" stroke="#fff" stroke-width="2"><path d="M8 2L3 7l5 5"/></svg></div>
<div class="arrow" style="left:1044px;background:var(--blue)"><svg width="12" height="14" viewBox="0 0 12 14" fill="none" stroke="#fff" stroke-width="2"><path d="M4 2l5 5-5 5"/></svg></div>

<section class="lower" role="img" aria-label="Faded office scene blending into blue"></section>
<h2 class="section-title" style="top:2597px">OUR <b>PARTNER</b></h2>
<div class="partner" style="left:218px"><strong>318 Builds Inc.</strong></div>
<div class="partner" style="left:415px"><strong>Norvixa</strong><span>Equipment Leasing Inc.</span></div>
<div class="partner" style="left:613px"><strong>firmstance</strong></div>
<div class="partner" style="left:809px"><strong>GSH</strong><span>DENTAL SERVICES LTD.</span></div>

<div class="contact-card"></div>
<h2 class="section-title" style="top:2861px">CONTACT <b>US</b></h2>
<div class="field" style="left:306px;top:2931px;width:288px">First Name</div>
<div class="field" style="left:602px;top:2931px;width:288px">Company Email</div>
<div class="field" style="left:306px;top:2983px;width:288px">Phone number</div>
<div class="field" style="left:602px;top:2983px;width:288px">Address</div>
<div class="field" style="left:306px;top:3037px;width:584px;height:104px">Send message</div>
<div class="btn" style="left:541px;top:3169px;width:118px;height:34px">Submit</div>

<div class="contact-info" style="left:141px">
  <span class="info-icon"><svg width="16" height="16" viewBox="0 0 16 16" fill="#fff"><path d="M3 1l3 3-2 2q2 4 6 6l2-2 3 3-2 2Q5 14 1 3z"/></svg></span>
  <div><b>Call us:</b><br>123 456 7890</div>
</div>
<span class="info-sep" style="left:352px"></span>
<div class="contact-info" style="left:417px">
  <span class="info-icon"><svg width="14" height="18" viewBox="0 0 14 18" fill="none" stroke="#fff" stroke-width="2"><path d="M7 17s6-6 6-10A6 6 0 0 0 1 7c0 4 6 10 6 10z"/><circle cx="7" cy="7" r="2"/></svg></span>
  <div>Lorem Ipsum Dolor Site 123456<br>#123456, Lorem ipsum</div>
</div>
<span class="info-sep" style="left:769px"></span>
<div class="contact-info" style="left:831px">
  <span class="info-icon"><svg width="16" height="12" viewBox="0 0 16 12" fill="none" stroke="#fff" stroke-width="2"><rect x="1" y="1" width="14" height="10"/><path d="M1 1l7 6 7-6"/></svg></span>
  <div><b>Email us:</b><br>info@velcorahealth.ca</div>
</div>

<footer class="bottom-bar">
  <span class="copy">© 2020 Velcorahealth Investment Medical. All Rights Reserved.</span>
  <span class="dot" style="left:955px"></span>
  <span class="dot" style="left:984px"></span>
  <span class="dot" style="left:1014px"></span>
  <span class="dot" style="left:1043px"></span>
</footer>

</body>
</html>
```